Brell Stone Company Business Cards

Front and Back Business Card - logo and text setup - cool design. I need workable photoshop or illustrator files so I can setup each employee card with design that is created
Updates

Hi everyone, thank you for the great entries. Please no more white and blue cards - there are so many already - black and silver only now please. thanks!

Target Market(s)

Construction Industry - Facility Managers

Industry/Entity Type

Construction

Contact Information for Business Card

I really like contemporary simplistic looks - clean neat....not opposed to seeing some black backrounds

Requirements
Must have
• Logo/website address with design on front only - www.brellstone-example.com (logo attached)
• Back:
• Name/Title/Company Address/Phone/email address
Nice to have
• Cool design
Should not have
• Nothing gimmicky like Fire or Water - since we are a Fire Protection company - it has all been done

```html
<!DOCTYPE html>
<html lang="en">
<head>
<meta charset="utf-8">
<title>Brell Stone Company Business Cards</title>
<link rel="stylesheet" href="https://fonts.googleapis.com/css2?family=Lato:wght@400;900&display=swap">
<style>
  :root {
    --page: #d4d4d4;
    --card: #232323;
    --blue: #2a4a8a;
    --orange: #f0492f;
    --text: #f2f2f2;
  }
  * { box-sizing: border-box; margin: 0; padding: 0; }
  html, body { width: 1200px; height: 1200px; overflow: hidden; }
  body {
    background: var(--page);
    font-family: 'Lato', sans-serif;
    position: relative;
  }
  .card {
    position: absolute;
    left: 250px;
    width: 707px;
    height: 404px;
    background: var(--card);
    color: var(--text);
  }
  .card--front { top: 144px; }
  .card--back { top: 582px; }

  .brand {
    display: flex;
    align-items: center;
    gap: 14px;
    font-weight: 900;
    color: var(--orange);
    letter-spacing: -0.5px;
    white-space: nowrap;
  }
  .brand__mark { background: var(--blue); flex: none; }

  .card--front .brand {
    position: absolute;
    top: 158px;
    left: 0; right: 0;
    justify-content: center;
    font-size: 66px;
    line-height: 80px;
  }
  .card--front .brand__mark { width: 30px; height: 30px; }
  .card--front .website {
    position: absolute;
    top: 343px;
    left: 0; right: 0;
    text-align: center;
    font-size: 21px;
    color: var(--orange);
  }

  .card--back .brand {
    position: absolute;
    top: 48px;
    right: 41px;
    font-size: 46px;
    line-height: 56px;
    gap: 10px;
  }
  .card--back .brand__mark { width: 20px; height: 20px; }

  .person { position: absolute; left: 38px; top: 220px; right: 41px; }
  .person__name { font-size: 22px; line-height: 28px; }
  .person__first { color: var(--blue); }
  .person__last { color: var(--orange); }
  .person__role {
    display: flex;
    align-items: center;
    gap: 14px;
    font-size: 17px;
    line-height: 22px;
  }
  .person__rule { flex: 1; height: 1.5px; background: var(--orange); margin-top: 4px; }

  .contacts { position: absolute; left: 38px; top: 284px; list-style: none; }
  .contacts li {
    display: flex;
    align-items: center;
    gap: 9px;
    font-size: 17px;
    line-height: 21px;
  }
  .contacts svg { width: 13px; height: 13px; fill: var(--orange); flex: none; }
  .accent { color: var(--orange); }

  .address {
    position: absolute;
    right: 41px;
    top: 326px;
    text-align: right;
    font-size: 17px;
    line-height: 21px;
    font-style: normal;
  }
</style>
</head>
<body>
  <section class="card card--front" aria-label="Card front">
    <div class="brand"><span class="brand__mark"></span>Brell Stone</div>
    <p class="website">www.brellstone-example.com</p>
  </section>

  <section class="card card--back" aria-label="Card back">
    <div class="brand"><span class="brand__mark"></span>Brell Stone</div>

    <div class="person">
      <p class="person__name"><span class="person__first">Dana</span> <span class="person__last">Merrow</span></p>
      <p class="person__role">Director <span class="person__rule"></span></p>
    </div>

    <ul class="contacts">
      <li>
        <svg viewBox="0 0 16 16" aria-hidden="true"><path d="M3.5 1l2.5 3-1.5 2c1 2 3 4 5 5l2-1.5 3 2.5-1.5 2.5C7.5 15 1 8.5 1.5 2.5z"/></svg>
        (555) 014-2231
      </li>
      <li>
        <svg viewBox="0 0 16 16" aria-hidden="true"><path d="M4 1h8v4H4zM1 6h14v6h-3v3H4v-3H1zM5 10v4h6v-4z"/></svg>
        (555) 014-2238
      </li>
      <li>
        <svg viewBox="0 0 16 16" aria-hidden="true"><path d="M1 3h14v1L8 9 1 4zM1 6l7 5 7-5v7H1z"/></svg>
        info@brellstone-example.com
      </li>
      <li>
        <svg viewBox="0 0 16 16" aria-hidden="true"><path d="M8 1a7 7 0 1 0 0 14A7 7 0 0 0 8 1zm0 1.5c.8 0 1.8 1.8 2 4.5H6c.2-2.7 1.2-4.5 2-4.5zM2.6 7h2C4.7 5 5 3.8 5.5 3A5.5 5.5 0 0 0 2.6 7zm8.8 0h2A5.5 5.5 0 0 0 10.5 3c.5.8.8 2 .9 4zM2.6 9a5.5 5.5 0 0 0 2.9 4c-.5-.8-.8-2-.9-4zm3.4 0c.2 2.7 1.2 4.5 2 4.5s1.8-1.8 2-4.5zm5.4 0c-.1 2-.4 3.2-.9 4a5.5 5.5 0 0 0 2.9-4z"/></svg>
        <span>www.<span class="accent">brellstone-example</span>.com</span>
      </li>
    </ul>

    <address class="address">48 Fieldstone Way<br>Harbor Point, NY 10000</address>
  </section>
</body>
</html>
```